Wordpress Design for a Digital Management Consulting Business

I need a simple Wordpress Design and someone to set it up for a new boutique management consulting business called Quillon Advisory that specialises in providing strategic advice to help grow digital businesses. It covers business strategy, marketing strategy, digital strategy, web product development, marketing campaigns, social, search, etc. From strategy to implementation.

URL is: quillonadvisory.com.au

My professional background is here: au.linkedin.com/in/hollyprenwick

Competitors: other boutique digital/marketing management consulting businesses in Australia

The logos, colours and fonts are attached.

I would like the site to convey a business that is Smart/intelligent, Contemporary, Progressive, Digital, Energetic, Friendly.

The objective of the site is to educate visitors about what Quillon Advisory does and encourage them to contact me for more information. It will be very light on content.

Target Market(s)

CEOs/Managing Directors, General Managers, Marketing Directors

Industry/Entity Type

Management Consulting

Font styles to use
Sans Serif

Colors
e34197
5c5c5c
000000

Requirements
Must have
• Site design requirements:
• Choose an appropriate Wordpress template, set it up for me and let me be able to edit it ongoing.
• It should use lots of images - these can be inspirational and not necessarily tied directly to the work
• Pink should feature, but not be the dominant colour.
• Site structure should be:
• 1. Home page - image led with horizontal navigation. Text beneath and images to describe the services.
• 2. About page - with space to write text and insert a picture of the Director
• 3. Services - with space to highlight services either as a list or graphically with text
• 4. Contact page - with space to write text and add email links, etc.
• Should have horizontal navigation
• It should have the flexibility to add another page
Nice to have
• Use the tree icon somehow in the design - consider in the background enlarged
• Use pink, grey, black from logo. Can introduce another complimentary colour if necessary.
• Can introduce another complimentary font to go with the logo font.
Should not have
• Use cliched business images and icons, eg. business suits, hand shakes, business men, business ties.

```html
<!DOCTYPE html>
<html lang="en">
<head>
<meta charset="utf-8">
<title>Quillon Advisory</title>
<link href="https://fonts.googleapis.com/css2?family=Open+Sans:wght@300;400;600;700&display=swap" rel="stylesheet">
<style>
:root{
  --pink:#e34197;
  --pink-dark:#c9327f;
  --grey:#5c5c5c;
  --grey-dark:#454545;
  --grey-light:#ececec;
  --black:#000;
  --white:#fff;
  --text:#555;
}
*{box-sizing:border-box;margin:0;padding:0}
html,body{width:1200px;height:2356px;overflow:hidden}
body{font-family:"Open Sans",Arial,sans-serif;color:var(--text);background:var(--white)}
.site{width:1200px;height:2356px;position:relative}

/* header */
.masthead{height:120px;position:relative}
.brand{position:absolute;left:100px;top:22px;display:flex;align-items:center;gap:14px;color:var(--pink);font-weight:600}
.brand-dot{width:64px;height:64px;border-radius:50%;background:var(--pink)}
.brand-name{line-height:1}
.brand-name .main{display:block;font-size:46px;letter-spacing:2px}
.brand-name .sub{display:block;font-size:20px;letter-spacing:6px;margin-top:4px}

.main-nav{height:48px;background:var(--pink);display:flex;padding-left:116px}
.main-nav a{color:var(--white);text-decoration:none;font-size:15px;line-height:48px;padding:0 28px;text-transform:uppercase}
.main-nav a.current{background:var(--black)}

/* hero */
.hero{height:492px;position:relative;background:linear-gradient(110deg,#f4f4f4 0%,#e2e4e8 35%,#c9ccd2 60%,#eceef0 100%)}
.hero-intro{position:absolute;left:100px;top:100px;width:460px;padding:14px 18px 20px;background:rgba(255,255,255,.72)}
.hero-intro h1{font-size:38px;font-weight:400;color:#111;margin-bottom:10px}
.hero-intro p{font-size:17px;line-height:1.45;color:#222;margin-bottom:18px}
.btn-row{display:flex}
.btn{background:var(--pink);color:var(--white);font-size:15px;font-weight:600;padding:0 16px;line-height:36px}
.btn-arrow{width:36px;height:36px;background:var(--grey);display:flex;align-items:center;justify-content:center}

/* services */
.services{height:540px;padding-top:70px;text-align:center}
.section-title{font-size:40px;font-weight:400;color:var(--pink);letter-spacing:1px}
.section-lead{font-size:15px;color:#777;margin-top:8px}
.card-row{display:flex;justify-content:center;gap:40px;margin-top:40px}
.service-card{width:320px;background:var(--white);box-shadow:0 2px 6px rgba(0,0,0,.18);border-bottom:4px solid var(--pink);text-align:center}
.service-card .media{height:150px;background:linear-gradient(135deg,#e8eaee,#aab2bd)}
.service-card h3{font-size:25px;font-weight:400;color:#222;margin:12px 0 6px}
.service-card p{font-size:14px;line-height:1.45;padding:0 26px 18px;color:#666}

/* what we do */
.approach{height:540px;background:var(--grey-dark);padding-top:62px;text-align:center}
.approach .section-title{color:var(--white)}
.approach .card-row{margin-top:44px}
.approach-card{width:320px;background:var(--white);text-align:center}
.approach-card .media{height:130px;background:linear-gradient(135deg,#dfe3e8,#8e98a6)}
.approach-card h3{background:var(--pink);color:var(--white);font-size:21px;font-weight:400;line-height:1.1;height:52px;display:flex;align-items:center;justify-content:center;padding:0 20px}
.approach-card p{font-size:14px;line-height:1.45;padding:22px 26px 26px;color:#666}

/* articles */
.articles{height:308px;background:var(--grey-light);padding:52px 100px 0}
.articles h2{font-size:38px;font-weight:400;color:#222}
.article-row{display:flex;gap:60px;margin-top:28px}
.article-item{display:flex;gap:20px;width:470px}
.article-item .thumb{width:160px;height:104px;flex:none;background:linear-gradient(135deg,#d4d8de,#7d8794)}
.article-meta{font-size:14px;color:#333;margin-bottom:6px}
.article-item p{font-size:13px;line-height:1.5;color:#666}
.article-item .byline{color:var(--pink);font-size:12px;margin-top:6px}

/* footer */
.site-footer{height:264px;background:#111;padding:32px 100px 0;display:flex;color:#ddd}
.footer-col h4{font-size:34px;font-weight:400;color:var(--white);margin-bottom:18px}
.footer-col ul{list-style:none}
.footer-col li{font-size:14px;line-height:25px}
.footer-col li::before{content:"›";color:var(--pink);margin-right:8px}
.col-links{width:200px}
.col-services{width:510px}
.col-services .lists{display:flex;gap:70px}
.contact-line{display:flex;align-items:center;gap:12px;font-size:14px;line-height:34px}
.social{display:flex;gap:10px;margin-top:14px}
.social span{width:26px;height:26px;border-radius:50%;border:2px solid #999}

.copyright{height:44px;background:var(--pink);color:var(--white);font-size:13px;text-align:center;line-height:44px}
</style>
</head>
<body>
<div class="site">
  <header class="masthead">
    <div class="brand">
      <span class="brand-dot"></span>
      <span class="brand-name"><span class="main">QUILLON</span><span class="sub">ADVISORY</span></span>
    </div>
  </header>
  <nav class="main-nav">
    <a class="current" href="#">Home</a>
    <a href="#">Our Services</a>
    <a href="#">About Us</a>
    <a href="#">Clients</a>
    <a href="#">Contact Us</a>
  </nav>

  <section class="hero" role="img" aria-label="Photo of a hand touching a tablet screen">
    <div class="hero-intro">
      <h1>Quillon Advisory</h1>
      <p>Boutique management consulting company advising digital businesses across business, product and marketing strategy.</p>
      <div class="btn-row">
        <span class="btn">Read More</span>
        <span class="btn-arrow"><svg width="12" height="12" viewBox="0 0 12 12"><path d="M4 2l4 4-4 4" stroke="#fff" stroke-width="2" fill="none"/></svg></span>
      </div>
    </div>
  </section>

  <section class="services">
    <h2 class="section-title">OUR SERVICES</h2>
    <p class="section-lead">Quillon Advisory provides a range of services from strategy through to implementation including;</p>
    <div class="card-row">
      <article class="service-card">
        <div class="media" role="img" aria-label="Photo of charts and a laptop on a desk"></div>
        <h3>Digital Strategy</h3>
        <p>Lorem Ipsum has been the industry's standard dummy text ever since the 1500s, when an unknown printer.</p>
      </article>
      <article class="service-card">
        <div class="media" role="img" aria-label="Photo of a person working at a desk"></div>
        <h3>Marketing Strategy</h3>
        <p>Lorem Ipsum has been the industry's standard dummy text ever since the 1500s, when an unknown printer.</p>
      </article>
      <article class="service-card">
        <div class="media" role="img" aria-label="Photo of a laptop and devices"></div>
        <h3>Digital Transformation</h3>
        <p>Lorem Ipsum has been the industry's standard dummy text ever since the 1500s, when an unknown printer.</p>
      </article>
    </div>
  </section>

  <section class="approach">
    <h2 class="section-title">WHAT WE DO</h2>
    <div class="card-row">
      <article class="approach-card">
        <div class="media" role="img" aria-label="Photo of a team meeting"></div>
        <h3>Strategic Thinking</h3>
        <p>Lorem Ipsum has been the industry's standard dummy text ever since the 1500s, when an unknown printer.</p>
      </article>
      <article class="approach-card">
        <div class="media" role="img" aria-label="Photo of hands reviewing documents"></div>
        <h3>Analytical Approach</h3>
        <p>Lorem Ipsum has been the industry's standard dummy text ever since the 1500s, when an unknown printer.</p>
      </article>
      <article class="approach-card">
        <div class="media" role="img" aria-label="Photo of a presenter with a group"></div>
        <h3>End to end project Management</h3>
        <p>Lorem Ipsum has been the industry's standard dummy text ever since the 1500s, when an unknown printer.</p>
      </article>
    </div>
  </section>

  <section class="articles">
    <h2>Article</h2>
    <div class="article-row">
      <article class="article-item">
        <div class="thumb" role="img" aria-label="Photo of people at a laptop"></div>
        <div>
          <div class="article-meta">26 May '14, 06:00pm in Quillon</div>
          <p>When an unknown printer took a galley of type and scrambled it to make a type specimen book.</p>
          <div class="byline">Posted by Nadia Collins</div>
        </div>
      </article>
      <article class="article-item">
        <div class="thumb" role="img" aria-label="Photo of a meeting around a table"></div>
        <div>
          <div class="article-meta">26 May '14, 06:00pm in Quillon</div>
          <p>When an unknown printer took a galley of type and scrambled it to make a type specimen book.</p>
          <div class="byline">Posted by Nadia Collins</div>
        </div>
      </article>
    </div>
  </section>

  <footer class="site-footer">
    <div class="footer-col col-links">
      <h4>Links</h4>
      <ul><li>Home</li><li>Our Services</li><li>About Us</li><li>Clients</li><li>Contact Us</li></ul>
    </div>
    <div class="footer-col col-services">
      <h4>Services</h4>
      <div class="lists">
        <ul><li>Business Strategy</li><li>Digital Strategy</li><li>Marketing Strategy</li><li>Product Strategy</li><li>Marketing Campaigns</li></ul>
        <ul><li>Product Management</li><li>Digital Marketing</li><li>Search/SEM Strategy</li><li>Content Marketing</li><li>New Product launches</li></ul>
      </div>
    </div>
    <div class="footer-col col-contact">
      <h4>Contact Us</h4>
      <div class="contact-line">
        <svg width="16" height="16" viewBox="0 0 16 16"><path d="M3 1h3l1 4-2 1c1 2 3 4 5 5l1-2 4 1v3c0 1-1 2-2 2C7 15 1 9 1 3c0-1 1-2 2-2z" fill="#ddd"/></svg>
        <span>Holly Prenwick &nbsp; 0412 555 018</span>
      </div>
      <div class="contact-line">
        <svg width="16" height="16" viewBox="0 0 16 16"><rect x="1" y="3" width="14" height="10" fill="none" stroke="#ddd" stroke-width="1.5"/><path d="M1 3l7 6 7-6" fill="none" stroke="#ddd" stroke-width="1.5"/></svg>
        <span>holly@quillonadvisory.com.au</span>
      </div>
      <div class="social"><span></span><span></span><span></span><span></span></div>
    </div>
  </footer>
  <div class="copyright">© 2015 Copyright Quillon Advisory Pty Ltd. All Rights Reserved</div>
</div>
</body>
</html>
```